ro dun magazine

just need coupons of real customers made for my magazine, I have the layout or temp lets of the magazine i just need the coupons to be made and plug-in. i have examples, of the ads or coupons, I'm sure they will need to redone. and in a section of the magazine their in a church directory. with this section , i need the pic of the pastor plug in with their church information and in do have some ex-samples of that as well. with the websites of the businesses. if you need to grab an image from their site . you'll be able to do so. all of the business are in the upload section , these are small base business so a lot of the ads and logos need redone any way . so i will look at it and let you know.

P.S with the new coupons and logos I'm trying to impress these customers to stay with the magazine

Target Market(s)

small businesses

Requirements
Must have
• good graphics
Should not have
• not pixelated graphics

```html
<!DOCTYPE html>
<html lang="en">
<head>
<meta charset="utf-8">
<title>We Let Church Riverton – Directory Card</title>
<link rel="stylesheet" href="https://fonts.googleapis.com/css2?family=Arimo:wght@400;700&display=swap">
<style>
  :root {
    --backdrop: #808080;
    --card: #ffffff;
    --gold: #d09d33;
    --brown: #9b6631;
    --ink: #1c1a1a;
    --photo-dark: #1f2a44;
    --photo-teal: #2f6b6a;
  }
  html, body {
    margin: 0;
    padding: 0;
    width: 1200px;
    height: 1200px;
    overflow: hidden;
    background: var(--backdrop);
    font-family: "Arimo", Arial, sans-serif;
  }
  .directory-card {
    position: absolute;
    left: 59px;
    top: 294px;
    width: 1082px;
    height: 612px;
    background: var(--card);
    overflow: hidden;
  }
  .accent-band {
    position: absolute;
    right: 0;
    top: 0;
    width: 243px;
    height: 100%;
    background: var(--gold);
  }
  .pastor-photo {
    position: absolute;
    left: 691px;
    top: 159px;
    width: 391px;
    height: 453px;
    display: block;
  }
  .church-info {
    position: absolute;
    left: 0;
    width: 864px;
    text-align: center;
  }
  .church-name {
    top: 78px;
    margin: 0;
    font-size: 37px;
    font-weight: 700;
    color: var(--brown);
    letter-spacing: -0.2px;
  }
  .church-address {
    top: 130px;
    margin: 0;
    font-size: 25px;
    line-height: 33px;
    color: var(--ink);
    font-weight: 400;
  }
  .pastor-name {
    top: 400px;
    margin: 0;
    font-size: 25px;
    font-weight: 700;
    color: var(--ink);
    letter-spacing: 0.3px;
  }
  .service-times {
    top: 446px;
    margin: 0;
    font-size: 21px;
    color: var(--ink);
  }
</style>
</head>
<body>
  <section class="directory-card">
    <div class="accent-band"></div>

    <h1 class="church-info church-name">We Let Church Riverton (wlc-rvt)</h1>
    <p class="church-info church-address">4580 MAPLE STREET , RIVERTON,PA.10000<br>(555) 014-2873</p>

    <h2 class="church-info pastor-name">REVEREND RO DUN</h2>
    <p class="church-info service-times">SUNDAY WORSHIP SERVICE AT 8 MA &amp; 10:45 AM</p>

    <svg class="pastor-photo" viewBox="0 0 391 453" role="img" aria-label="Photo of the pastor and his wife standing together, smiling">
      <defs>
        <linearGradient id="photoTone" x1="0" y1="0" x2="1" y2="1">
          <stop offset="0" stop-color="var(--photo-dark)"/>
          <stop offset="1" stop-color="var(--photo-teal)"/>
        </linearGradient>
      </defs>
      <rect width="391" height="453" fill="url(#photoTone)"/>
    </svg>
  </section>
</body>
</html>
```